Brindlewick Cellars Winery… For non-interventionist winemakers, wine-making begins in the

Need a new website for my new winery…previous one lost in divorce to my cheating ex wife…sigh. Calling it Brindlewick Cellars. Want it to look like a wedding sight…calligraphy writing…black and white…with some black roses…want the look of a invitational wedding site…celebratory! We employ a combination of modern techniques and old world traditions, practicing both the cuvee and "field blending" methods, to create a range of distinctive varietals. To ensure flawless berries reach the fermentation process, we hand-sort grapes as soon as we get them into the winery. Our open-top, double-jacketed fermenters allow precise temperature control during "cold soak" periods and primary fermentation -- essential for color, flavor, and tannin extraction. Occasional délestage ("rack & return") aerates the wine. After ratchet basket pressing, we age our wines in French oak barrels for at least 18 months; minimal racking lets wine clarify naturally. Patience, sagacity, gumption, and a balance between both received methods (classic and modern) and ingenuity are foundations for crafting the world-class wines offered by our small, family-run artisanal winery here in the beautiful Walla Walla valley, located beneath the Blue Mountains in eastern Washington

Target Market(s)

Wine drinkers/broken hearts

Industry/Entity Type

Winery

Number of Pages Required

4 page

Font styles to use
Script

Colors

Designer to choose only greyscale colors for use in the design.

Requirements
Must have
• Black roses… From our Walla Walla valley boutique winery here in the Pacific Northwest, we offer a range of premium reds, whites, ice wines, late harvest wines, brandies, grappas, and specialty spirits. We embrace sustainable farming methods on our estate vineyard and source fruit from growers who share our commitment to biodiversity. A great bottle of wine begins with the vine! For our "green wines," we practice innovative eco-friendly techniques, aim for Earth-friendly packaging, and donate a portion of our after-profit proceeds to environmental concerns. Though we appreciate ratings, we're less interested in numbers and more in the approval of our palettes and those of trusted friends, as well as accolades from loyal customers near and far. We handcraft what we hope will become your cult wines, often well into the night, humbled by the calls of barn owls who give our cellar its name.
Nice to have
• Page to list varieties…Tamarack Tokaji, Lanternfall Lambrusco, Cobblemoor Claret

```html
<!DOCTYPE html>
<html lang="en">
<head>
<meta charset="utf-8">
<title>Brindlewick Cellars</title>
<link rel="stylesheet" href="https://fonts.googleapis.com/css2?family=Lobster&family=Josefin+Sans:ital,wght@0,300;0,400;0,600;1,300&display=swap">
<style>
:root{
  --ink:#111;
  --black:#000;
  --white:#fff;
  --text:#4a4a4a;
  --muted:#6b6b6b;
  --panel:#dcdedf;
  --line:#b5b5b5;
  --rose-dark:#434a4b;
  --rose-mid:#6f7778;
  --rose-light:#9aa2a3;
}
*{margin:0;padding:0;box-sizing:border-box}
html,body{width:1200px;height:2611px;overflow:hidden;background:var(--white)}
body{position:relative;font-family:"Josefin Sans",sans-serif;color:var(--text)}

.header{position:absolute;left:0;top:0;width:1200px;height:96px;background:var(--white)}
.brand{position:absolute;left:232px;top:26px;font-family:"Lobster",cursive;font-size:38px;color:#3c3c3c;line-height:1}
.nav{position:absolute;left:750px;top:36px;display:flex;gap:26px;font-family:"Lobster",cursive;font-size:17px;color:var(--ink)}
.nav a{color:inherit;text-decoration:none;padding-bottom:4px}
.nav a.active{border-bottom:2px solid var(--ink)}

.hero{position:absolute;left:0;top:96px;width:1200px;height:582px;background:radial-gradient(ellipse 420px 380px at 42% 35%,#707070 0%,#2e2e2e 45%,#060606 80%),#050505}
.hero-title{position:absolute;left:640px;top:262px;font-family:"Lobster",cursive;font-size:62px;color:var(--white);line-height:1;white-space:nowrap}
.hero-sub{position:absolute;left:640px;top:352px;font-weight:300;font-size:46px;color:var(--white);line-height:1}
.btn-outline{position:absolute;left:640px;top:428px;width:160px;height:46px;border:3px solid var(--white);border-radius:23px;color:var(--white);font-size:17px;display:flex;align-items:center;justify-content:center;font-style:italic;font-weight:300}
.dots{position:absolute;left:1098px;top:600px;display:flex;gap:8px;align-items:center}
.dots span{width:10px;height:10px;border-radius:50%;background:var(--white)}
.dots span.on{width:14px;height:14px;background:transparent;border:2px solid var(--white)}
.arch{position:absolute;left:0;top:540px}

.rose-corner{position:absolute;pointer-events:none}
.rose-corner.top-left{left:0;top:0;width:190px;height:220px;background:radial-gradient(ellipse 120px 150px at 0% 20%,var(--rose-dark) 0%,var(--rose-mid) 45%,rgba(154,162,163,.5) 70%,rgba(255,255,255,0) 100%)}
.rose-corner.top-right{right:0;top:0;width:230px;height:220px;background:radial-gradient(ellipse 150px 150px at 100% 20%,var(--rose-dark) 0%,var(--rose-mid) 45%,rgba(154,162,163,.5) 70%,rgba(255,255,255,0) 100%)}
.rose-corner.bottom-left{left:0;top:2250px;width:240px;height:209px;background:radial-gradient(ellipse 170px 160px at 10% 100%,var(--rose-dark) 0%,var(--rose-mid) 45%,rgba(154,162,163,.5) 70%,rgba(255,255,255,0) 100%)}
.rose-corner.bottom-right{right:0;top:2250px;width:250px;height:209px;background:radial-gradient(ellipse 170px 160px at 90% 100%,var(--rose-dark) 0%,var(--rose-mid) 45%,rgba(154,162,163,.5) 70%,rgba(255,255,255,0) 100%)}

.intro{position:absolute;left:198px;top:656px;width:803px;font-size:14px;line-height:27.2px;font-style:italic;font-weight:300;text-align:justify;text-align-last:center;color:var(--text)}

.wine{position:absolute;top:872px;width:328px;text-align:center}
.wine .photo{width:328px;height:328px;border-radius:50%;border:8px solid var(--white);background:radial-gradient(circle at 50% 40%,#a0a0a0,#4a4a4a 60%,#141414)}
.wine h3{margin-top:10px;font-weight:600;font-size:24px;color:var(--ink);letter-spacing:.5px}

.about{position:absolute;left:30px;top:1316px;width:1139px;height:395px;border-radius:198px;background:var(--panel);overflow:hidden}
.about .rose-art{position:absolute;right:0;bottom:0;width:420px;height:330px;background:radial-gradient(ellipse 230px 170px at 80% 85%,#454b4c 0%,#6f7778 40%,rgba(220,222,223,0) 100%)}
.about h2{position:absolute;left:115px;top:48px;font-family:"Lobster",cursive;font-size:50px;font-weight:400;color:#222}
.about p{position:absolute;left:115px;top:114px;width:742px;font-size:14px;line-height:27.2px;font-style:italic;font-weight:300;text-align:justify;color:var(--text)}

.contact-title{position:absolute;left:0;top:1780px;width:1200px;text-align:center;font-family:"Lobster",cursive;font-size:50px;font-weight:400;color:var(--ink)}
.info{position:absolute;top:1880px;width:240px;text-align:center}
.info .icon{width:72px;height:72px;margin:0 auto;border-radius:50%;border:1.5px solid #777;display:flex;align-items:center;justify-content:center;background:var(--white);box-shadow:2px 3px 5px rgba(0,0,0,.15)}
.info .icon.solid{background:var(--black);border-color:var(--black)}
.info h4{margin-top:22px;font-weight:600;font-size:16px;letter-spacing:1px;color:#333}
.info p{margin-top:10px;font-size:14px;font-weight:300;font-style:italic;line-height:21px;color:var(--muted)}

.field{position:absolute;height:60px;border:2.5px solid var(--line);border-radius:30px;padding:23px 0 0 27px;font-size:16px;font-style:italic;font-weight:300;color:#333;line-height:1;background:var(--white)}
.field.message{height:92px;padding-top:22px}
.submit{position:absolute;left:543px;top:2367px;width:115px;height:42px;border-radius:21px;background:var(--black);color:var(--white);font-size:17px;font-style:italic;font-weight:300;display:flex;align-items:center;justify-content:center}

.footer{position:absolute;left:0;top:2459px;width:1200px;height:152px;background:var(--black)}
.social{position:absolute;left:509px;top:2488px;display:flex;gap:7px}
.social span{width:41px;height:41px;border-radius:50%;background:var(--white);border:2px solid #888;display:flex;align-items:center;justify-content:center;font-size:8px;font-weight:600;color:var(--ink);letter-spacing:.2px}
.copyright{position:absolute;left:0;top:2554px;width:1200px;text-align:center;color:var(--white);font-size:13px}
</style>
</head>
<body>

<section class="hero" role="img" aria-label="Black and white photo of red wine being poured from a bottle into a glass"></section>

<header class="header">
  <div class="brand">Brindlewick Cellars</div>
  <nav class="nav"><a class="active">Home</a><a>Wine</a><a>Contact</a></nav>
</header>

<div class="rose-corner top-left" role="img" aria-label="Cluster of black roses with leaves"></div>
<div class="rose-corner top-right" role="img" aria-label="Cluster of black roses with leaves"></div>

<div class="hero-title">Brindlewick Cellars</div>
<div class="hero-sub">Walla Walla Valley</div>
<div class="btn-outline">GET STARTED</div>
<div class="dots"><span></span><span class="on"></span><span></span></div>

<svg class="arch" width="1200" height="140" viewBox="0 0 1200 140">
  <path d="M143 138 C170 40 400 12 600 12 C800 12 1030 40 1058 138 Z" fill="#333"/>
  <path d="M147 138 C180 50 400 30 600 30 C800 30 1020 50 1054 138 Z" fill="#fff"/>
  <path d="M143 138 C170 40 400 12 600 12 C800 12 1030 40 1058 138" fill="none" stroke="#fff" stroke-width="2"/>
</svg>

<p class="intro">Black roses... From our Walla Walla valley boutique winery here in the Pacific Northwest, we offer a range of premium reds, whites, ice wines, late harvest wines, brandies, grappas, and specialty spirits. We embrace sustainable farming methods on our estate vineyard and source fruit from growers who share our commitment to biodiversity. A great bottle of wine begins with the vine! For our "green wines," we practice innovative eco-friendly techniques, aim for Earth-friendly packaging, and donate a portion of our after-profit proceeds to environmental concerns. Though we appreciate ratings, we're less interested in numbers and more in the approval of our palettes and those of trusted friends, as well as accolades from loyal customers near and far. We handcraft what we hope will become your cult wines, often well into the night, humbled by the calls of barn owls who give our cellar its name.</p>

<div class="wine" style="left:142px"><div class="photo" role="img" aria-label="Wine bottles lying beside bunches of grapes"></div><h3>Tamarack Tokaji</h3></div>
<div class="wine" style="left:436px"><div class="photo" role="img" aria-label="Two bottles and glasses in front of a vineyard"></div><h3>Lanternfall Lambrusco</h3></div>
<div class="wine" style="left:731px"><div class="photo" role="img" aria-label="Glass of red wine and bottle by an oak barrel"></div><h3>Cobblemoor Claret</h3></div>

<section class="about">
  <div class="rose-art" role="img" aria-label="Black roses with leaves"></div>
  <h2>About Us</h2>
  <p>We employ a combination of modern techniques and old world traditions, practicing both the cuvee and "field blending" methods, to create a range of distinctive varietals. To ensure flawless berries reach the fermentation process, we hand-sort grapes as soon as we get them into the winery. Our open-top, double-jacketed fermenters allow precise temperature control during "cold soak" periods and primary fermentation -- essential for color, flavor, and tannin extraction. Occasional délestage ("rack &amp; return") aerates the wine. After ratchet basket pressing, we age our wines in French oak barrels for at least 18 months; minimal racking lets wine clarify naturally. Patience, sagacity, gumption, and a balance between both received methods (classic and modern) and ingenuity are foundations for crafting the world-class wines offered by our small, family-run artisanal winery here in the beautiful Walla Walla valley, located beneath the Blue Mountains in eastern Washington</p>
</section>

<h2 class="contact-title">Contact</h2>

<div class="info" style="left:98px">
  <div class="icon"><svg width="26" height="26" viewBox="0 0 24 24"><path fill="#111" d="M6.6 10.8a15 15 0 0 0 6.6 6.6l2.2-2.2c.3-.3.7-.4 1-.2 1.1.4 2.3.6 3.6.6.6 0 1 .4 1 1V20c0 .6-.4 1-1 1A17 17 0 0 1 3 4c0-.6.4-1 1-1h3.5c.6 0 1 .4 1 1 0 1.3.2 2.5.6 3.6.1.3 0 .7-.2 1z"/></svg></div>
  <h4>PHONE</h4><p>(+428) 888 888 8888</p>
</div>
<div class="info" style="left:324px">
  <div class="icon"><svg width="22" height="30" viewBox="0 0 24 32"><path fill="#111" d="M12 0C5.4 0 0 5.4 0 12c0 9 12 20 12 20s12-11 12-20C24 5.4 18.6 0 12 0zm0 17a5 5 0 1 1 0-10 5 5 0 0 1 0 10z"/></svg></div>
  <h4>HEAD OFFICE</h4><p>123 west Dummy Car Street, Old City,<br>New State, USA. PO 4288</p>
</div>
<div class="info" style="left:603px">
  <div class="icon solid"><svg width="22" height="30" viewBox="0 0 24 32"><path fill="#fff" d="M12 0C5.4 0 0 5.4 0 12c0 9 12 20 12 20s12-11 12-20C24 5.4 18.6 0 12 0zm0 17a5 5 0 1 1 0-10 5 5 0 0 1 0 10z"/></svg></div>
  <h4>MAIN OFFICE</h4><p>123 west Dummy Car Street, Old City,<br>New State, USA. PO 4288</p>
</div>
<div class="info" style="left:851px">
  <div class="icon"><svg width="28" height="22" viewBox="0 0 28 22"><rect x="0" y="0" width="28" height="22" rx="3" fill="#111"/><path d="M2 3l12 9 12-9" fill="none" stroke="#fff" stroke-width="2"/></svg></div>
  <h4>EMAIL</h4><p>info@companyname.com</p>
</div>

<div class="rose-corner bottom-left" role="img" aria-label="Cluster of black roses with leaves"></div>
<div class="rose-corner bottom-right" role="img" aria-label="Cluster of black roses with leaves"></div>

<div class="field" style="left:232px;top:2097px;width:361px">Enter Name</div>
<div class="field" style="left:607px;top:2097px;width:362px">Enter Email</div>
<div class="field" style="left:232px;top:2176px;width:361px">Phone</div>
<div class="field" style="left:607px;top:2176px;width:362px">Address</div>
<div class="field message" style="left:232px;top:2255px;width:737px">Message</div>
<div class="submit">SUBMIT</div>

<footer class="footer"></footer>
<div class="social"><span>Vinyard</span><span>Chirp</span><span>Orbit</span><span>Nexa</span></div>
<div class="copyright">Copyrights © 2024 Brindlewick Cellars. All rights reserved &nbsp;|&nbsp; Privacy policy &nbsp;|&nbsp; Site Map &nbsp;|&nbsp; Disclaimer &nbsp;|&nbsp; Terms of use</div>

</body>
</html>
```